Landing Page / Waitlist

I would like a landing page for people to sign up for a waiting list. The text on the page should include (but is not limited to):
1) Main point: The accounting system you'll love
2) Secondary points:
a. Ruthlessly efficient
b. Quietly intelligent
c. Driven by AI
I've attached a file of our logo

The design should be simple, clean, and innovative - this is an ai company

```html
<!DOCTYPE html>
<html lang="en">
<head>
<meta charset="UTF-8">
<title>LedgerNova — Join the waitlist</title>
<link href="https://fonts.googleapis.com/css2?family=Poppins:wght@300;400;600;700&display=swap" rel="stylesheet">
<style>
  :root {
    --bg-deep: #05070c;
    --bg-navy: #0b1a2e;
    --glow-blue: #12324f;
    --glow-amber: #4a2a12;
    --brand-blue: #0aa0ff;
    --brand-blue-bright: #1fb0ff;
    --wordmark-grey: #9b9b9b;
    --text-white: #ffffff;
    --field-white: #ffffff;
    --placeholder-grey: #8a8a8a;
    --footer-grey: #a5a5a5;
  }
  * { margin: 0; padding: 0; box-sizing: border-box; }
  html, body {
    width: 1200px; height: 675px; overflow: hidden;
    background: var(--bg-deep);
    font-family: "Poppins", sans-serif;
  }
  .page {
    position: relative; width: 1200px; height: 675px; overflow: hidden;
    background: var(--bg-deep);
  }
  .backdrop {
    position: absolute; inset: 0;
    background:
      radial-gradient(ellipse 520px 160px at 560px 440px, rgba(120,60,20,0.55), transparent 70%),
      radial-gradient(ellipse 420px 200px at 880px 330px, rgba(30,90,120,0.45), transparent 70%),
      radial-gradient(ellipse 700px 300px at 200px 200px, rgba(18,50,80,0.5), transparent 70%),
      radial-gradient(ellipse 600px 300px at 1100px 500px, rgba(18,50,80,0.45), transparent 70%),
      linear-gradient(180deg, #04060a 0%, #070d18 55%, #05070c 100%);
  }
  .brand {
    position: absolute; left: 0; right: 0; top: 92px;
    display: flex; flex-direction: column; align-items: center;
  }
  .brand-mark {
    width: 64px; height: 64px; background: var(--brand-blue);
    margin-bottom: 26px;
  }
  .brand-name {
    font-weight: 600; font-size: 50px; line-height: 1;
    color: var(--wordmark-grey); letter-spacing: -1px;
  }
  .headline {
    position: absolute; left: 0; right: 0; top: 237px;
    text-align: center; font-size: 45px; line-height: 1.1;
    color: var(--brand-blue);
  }
  .headline strong { font-weight: 700; }
  .headline span { font-weight: 300; }
  .features { position: absolute; left: 0; right: 0; top: 322px; }
  .feature {
    position: absolute; width: 260px; margin-left: -130px;
    display: flex; flex-direction: column; align-items: center;
  }
  .feature svg { width: 74px; height: 74px; }
  .feature-label {
    margin-top: 14px; font-size: 22px; font-weight: 400;
    color: var(--text-white); white-space: nowrap;
  }
  .waitlist {
    position: absolute; left: 354px; top: 476px; width: 492px; height: 43px;
    display: flex; border-radius: 22px; overflow: hidden;
  }
  .email-field {
    flex: 0 0 310px; background: var(--field-white);
    display: flex; align-items: center; padding-left: 18px; gap: 12px;
    font-size: 11px; color: var(--placeholder-grey);
  }
  .join-button {
    flex: 1; background: var(--brand-blue-bright); border: none;
    color: var(--text-white); font-family: "Poppins", sans-serif;
    font-weight: 700; font-size: 19px; cursor: pointer;
  }
  .footer {
    position: absolute; left: 0; right: 0; top: 640px;
    text-align: center; font-size: 12.5px; color: var(--footer-grey);
  }
</style>
</head>
<body>
<main class="page">
  <div class="backdrop" role="img" aria-label="Dark space-like background with a glowing flowing particle wave in blue and amber tones"></div>

  <header class="brand">
    <div class="brand-mark"></div>
    <div class="brand-name">LedgerNova</div>
  </header>

  <h1 class="headline"><strong>The Accounting</strong> <span>System You'll Love</span></h1>

  <section class="features">
    <div class="feature" style="left:343px">
      <svg viewBox="0 0 74 74" fill="none" stroke="var(--brand-blue)" stroke-width="2.4" stroke-linecap="round" stroke-linejoin="round">
        <path d="M37 12a19 19 0 0 0-11 34.5c2 1.6 3 3.6 3 6V56h16v-3.5c0-2.4 1-4.4 3-6A19 19 0 0 0 37 12z"/>
        <path d="M30 61h14M32 66h10"/>
        <path d="M37 50V34M37 40c-6 0-9-4-9-10 6 0 9 4 9 10zM37 40c6 0 9-4 9-10-6 0-9 4-9 10z"/>
        <path d="M37 3v4M12 14l3 3M62 14l-3 3M4 33h4M66 33h4M10 52l3-2M64 52l-3-2"/>
      </svg>
      <div class="feature-label">Ruthlessly efficient</div>
    </div>
    <div class="feature" style="left:600px">
      <svg viewBox="0 0 74 74" fill="none" stroke="var(--brand-blue)" stroke-width="2.4" stroke-linecap="round" stroke-linejoin="round">
        <path d="M36 6c-5-2-11 0-13 5-6 0-10 5-9 10-5 3-6 10-2 14-4 4-3 11 2 14-1 6 4 11 10 11 2 5 8 7 12 5z"/>
        <path d="M36 6v60"/>
        <path d="M36 18h10l4-4M36 30h22M36 42h12l4 4M36 54h8l4 4"/>
        <circle cx="53" cy="12" r="3"/><circle cx="62" cy="30" r="3"/>
        <circle cx="55" cy="48" r="3"/><circle cx="51" cy="60" r="3"/>
      </svg>
      <div class="feature-label">Quietly intelligent</div>
    </div>
    <div class="feature" style="left:838px">
      <svg viewBox="0 0 74 74" fill="none" stroke="var(--brand-blue)" stroke-width="2.4" stroke-linecap="round">
        <ellipse cx="37" cy="37" rx="34" ry="13"/>
        <ellipse cx="37" cy="37" rx="34" ry="13" transform="rotate(60 37 37)"/>
        <ellipse cx="37" cy="37" rx="34" ry="13" transform="rotate(-60 37 37)"/>
        <text x="37" y="44" text-anchor="middle" font-family="Poppins, sans-serif" font-size="20" font-weight="400" fill="var(--brand-blue)" stroke="none">AI</text>
      </svg>
      <div class="feature-label">Driven by AI</div>
    </div>
  </section>

  <form class="waitlist">
    <label class="email-field">
      <svg width="11" height="9" viewBox="0 0 11 9" fill="none" stroke="#222" stroke-width="1.2"><rect x="0.6" y="0.6" width="9.8" height="7.8" rx="1"/><path d="M1 1.5l4.5 3.5L10 1.5"/></svg>
      Enter you email
    </label>
    <button class="join-button" type="button">Join the waitlist</button>
  </form>

  <footer class="footer">© 2025 | www.ledgernova.com</footer>
</main>
</body>
</html>
```